Ridgeline Journeys business card

please see website
www.ridgelinejourneys.comau

info needed on card
Curtis Halvey
Ph
email
Adventure Riding GPS trails

please use my logo and colours off my site

Curtis Halvey
curtis@ridgelinejourneys.com

```html
<!DOCTYPE html>
<html lang="en">
<head>
<meta charset="utf-8">
<title>Ridgeline Journeys business card</title>
<link href="https://fonts.googleapis.com/css2?family=Roboto+Condensed:wght@400;700&display=swap" rel="stylesheet">
<style>
  :root {
    --stage: #1e1e1e;
    --card-dark: #0b0b0b;
    --card-light: #ffffff;
    --ink: #1a1a1a;
    --ink-soft: #555555;
    --accent: #f6d21c;
    --on-dark: #f2f2f2;
  }
  * { margin: 0; padding: 0; box-sizing: border-box; }
  html, body {
    width: 1200px; height: 750px; overflow: hidden;
    background: var(--stage);
    font-family: "Roboto Condensed", Arial, sans-serif;
  }
  .stage { position: relative; width: 1200px; height: 750px; }
  .card {
    position: absolute; width: 520px; height: 297px;
    box-shadow: 0 14px 30px rgba(0,0,0,.55);
  }
  .card--back {
    left: 80px; top: 90px;
    background: linear-gradient(160deg, #1a1a1a 0%, var(--card-dark) 55%);
    display: flex; flex-direction: column; align-items: center; justify-content: center;
    gap: 14px;
  }
  .card--front {
    left: 600px; top: 363px;
    background: var(--card-light);
  }
  .brand { display: flex; align-items: center; gap: 12px; }
  .brand__dot { width: 26px; height: 26px; border-radius: 50%; background: var(--accent); }
  .brand__name {
    font-weight: 700; text-transform: uppercase; letter-spacing: .5px; line-height: 1;
  }
  .card--back .brand__name { color: var(--on-dark); font-size: 30px; }
  .card--back .tagline { color: var(--on-dark); font-size: 14px; letter-spacing: .4px; }

  .card--front .brand { position: absolute; left: 34px; top: 48px; }
  .card--front .brand__name { color: var(--ink); font-size: 30px; width: 170px; }
  .holder {
    position: absolute; right: 40px; top: 118px;
    color: var(--accent); font-size: 22px;
  }
  .contacts {
    position: absolute; left: 34px; bottom: 34px;
    list-style: none; color: var(--ink-soft); font-size: 13px;
  }
  .contacts li { display: flex; align-items: center; gap: 8px; margin-top: 5px; }
  .contacts li:first-child { font-size: 15px; color: var(--ink); }
  .contacts svg { width: 14px; height: 14px; flex: none; }
  .contacts .tagline { font-size: 16px; color: var(--ink-soft); margin-top: 8px; letter-spacing: .3px; }
</style>
</head>
<body>
<main class="stage">
  <section class="card card--back">
    <div class="brand">
      <span class="brand__dot"></span>
      <span class="brand__name">Ridgeline Journeys</span>
    </div>
    <p class="tagline">Adventure Riding GPS trails</p>
  </section>

  <section class="card card--front">
    <div class="brand">
      <span class="brand__dot"></span>
      <span class="brand__name">Ridgeline Journeys</span>
    </div>
    <p class="holder">Curtis Halvey</p>
    <ul class="contacts">
      <li>
        <svg viewBox="0 0 16 16" aria-hidden="true"><path fill="#f6d21c" d="M3.5 1.5l2.5 0 1 3.5-1.6 1.2a8 8 0 0 0 4.4 4.4L11 9l3.5 1v2.5c0 1-1 2-2 2A11 11 0 0 1 1.5 3.5c0-1 1-2 2-2z"/></svg>
        555 0142 7781
      </li>
      <li>
        <svg viewBox="0 0 16 16" aria-hidden="true"><rect x="1" y="3" width="14" height="10" rx="1" fill="#f6d21c"/><path d="M1.5 3.8L8 9l6.5-5.2" stroke="#fff" stroke-width="1.3" fill="none"/></svg>
        curtis@ridgelinejourneys.com
      </li>
      <li>
        <svg viewBox="0 0 16 16" aria-hidden="true"><circle cx="8" cy="8" r="6.5" fill="#f6d21c"/><path d="M1.5 8h13M8 1.5c-2.5 3-2.5 10 0 13M8 1.5c2.5 3 2.5 10 0 13" stroke="#fff" stroke-width="1" fill="none"/></svg>
        www.ridgelinejourneys.comau
      </li>
      <li class="tagline">Adventure Riding GPS trails</li>
    </ul>
  </section>
</main>
</body>
</html>
```